Keystone Trench Co Business Card*

Looking for a professional, clean and crisp business card

I am in the underground utilities industry and am just looking for a really impressive business card. I would like our card to be white with our symbol crisp and clear with it protruding. I also have a business partner that will require his name and info on the card once the design is set. I would like to have our website info on the card which is;
http://keystonetrenchco.example/

Contact Information for Business Card

Website, contact name, number and email

```html
<!DOCTYPE html>
<html lang="en">
<head>
<meta charset="utf-8">
<title>Keystone Trench Co — Business Card</title>
<link href="https://fonts.googleapis.com/css2?family=Roboto+Condensed:wght@400;700;800&display=swap" rel="stylesheet">
<style>
  :root {
    --bg: #e6e7e9;
    --card: #ffffff;
    --ink: #1f1f20;
    --blue: #3a62a8;
    --rule: #a9a9a9;
    --faint: #ecebeb;
  }
  * { margin: 0; padding: 0; box-sizing: border-box; }
  html, body { width: 1200px; height: 900px; overflow: hidden; }
  body {
    background: var(--bg);
    font-family: "Roboto Condensed", "Arial Narrow", sans-serif;
    color: var(--ink);
    position: relative;
  }
  .card {
    position: absolute;
    width: 620px;
    height: 354px;
    background: var(--card);
    box-shadow: 0 6px 18px rgba(0,0,0,0.12);
    overflow: hidden;
  }
  .card--front { left: 90px; top: 80px; }
  .card--back { left: 490px; top: 476px; }

  /* front */
  .brand-mark {
    position: absolute;
    left: 40px; top: 0; width: 200px; height: 100%;
    display: flex; align-items: center; justify-content: center;
    text-align: center;
  }
  .brand-name {
    font-weight: 800;
    font-size: 30px;
    line-height: 1.05;
    text-transform: uppercase;
    color: var(--ink);
    letter-spacing: 0.5px;
  }
  .divider {
    position: absolute;
    left: 268px; top: 112px;
    width: 1px; height: 150px;
    background: var(--rule);
  }
  .contact {
    position: absolute;
    left: 292px; top: 112px;
  }
  .contact__name {
    font-weight: 800;
    font-size: 21px;
    text-transform: uppercase;
    letter-spacing: 0.3px;
    line-height: 1;
  }
  .contact__role {
    font-weight: 700;
    font-size: 13px;
    color: var(--blue);
    text-transform: uppercase;
    margin-top: 4px;
    margin-bottom: 14px;
  }
  .contact__list { list-style: none; }
  .contact__item {
    display: flex; align-items: center;
    font-size: 14px;
    text-transform: uppercase;
    margin-bottom: 9px;
  }
  .contact__icon {
    width: 24px; height: 24px;
    background: var(--blue);
    display: flex; align-items: center; justify-content: center;
    margin-right: 12px;
    flex: none;
  }
  .band { position: absolute; right: 0; width: 46px; }
  .band--blue { top: 0; height: 130px; background: var(--blue); }
  .band--black { top: 152px; bottom: 0; background: var(--ink); }

  /* back */
  .back-decor {
    position: absolute;
    left: 50%; top: 50%;
    width: 420px; height: 420px;
    margin: -210px 0 0 -210px;
    border-radius: 50%;
    border: 14px solid var(--faint);
  }
  .back-name {
    position: absolute;
    inset: 0;
    display: flex; align-items: center; justify-content: center;
    font-weight: 800;
    font-size: 46px;
    text-transform: uppercase;
    color: var(--ink);
    letter-spacing: 1px;
  }
</style>
</head>
<body>
  <section class="card card--front" aria-label="Business card front">
    <div class="brand-mark"><span class="brand-name">Keystone<br>Trench Co</span></div>
    <div class="divider"></div>
    <div class="contact">
      <p class="contact__name">Dale Corrigan</p>
      <p class="contact__role">Owner</p>
      <ul class="contact__list">
        <li class="contact__item">
          <span class="contact__icon">
            <svg width="14" height="14" viewBox="0 0 24 24" aria-hidden="true"><path fill="#fff" d="M6.6 10.8a15 15 0 0 0 6.6 6.6l2.2-2.2a1 1 0 0 1 1-.25 11.4 11.4 0 0 0 3.6.57 1 1 0 0 1 1 1V20a1 1 0 0 1-1 1A17 17 0 0 1 3 4a1 1 0 0 1 1-1h3.5a1 1 0 0 1 1 1c0 1.25.2 2.45.57 3.57a1 1 0 0 1-.25 1z"/></svg>
          </span>555-014-2286
        </li>
        <li class="contact__item">
          <span class="contact__icon">
            <svg width="14" height="14" viewBox="0 0 24 24" aria-hidden="true"><rect x="3" y="6" width="18" height="12" fill="none" stroke="#fff" stroke-width="2"/><path d="M3 6l9 7 9-7" fill="none" stroke="#fff" stroke-width="2"/></svg>
          </span>dale@keystonetrenchco.example
        </li>
        <li class="contact__item">
          <span class="contact__icon">
            <svg width="14" height="14" viewBox="0 0 24 24" aria-hidden="true"><g fill="none" stroke="#fff" stroke-width="2"><circle cx="12" cy="12" r="9"/><ellipse cx="12" cy="12" rx="4" ry="9"/><path d="M3 12h18"/></g></svg>
          </span>www.keystonetrenchco.example
        </li>
      </ul>
    </div>
    <div class="band band--blue"></div>
    <div class="band band--black"></div>
  </section>

  <section class="card card--back" aria-label="Business card back">
    <div class="back-decor"></div>
    <div class="back-name">Keystone Trench Co</div>
  </section>
</body>
</html>
```